One pager digital ad-Corporate travel Manager

I need a design that is smooth, and business like. I don’t like basic generic designs that I can make my self. I’m looking for a sharp clean ad that clearly was made by a great designer. I need some bullet points in and the add to be clean. Here is a list of some content from our content writers. You can arrange and play with the words a bit.

*Budget*- having a travel management service will ensure that your company sticks to a budget which will help PROTECT your bottom line. Travel expenses often CAN BE COSTLY and having a SAVVY corporate travel manager handle YOUR TRAVEL ARRANGEMENTS will make sure that the travel expenses are kept under control.
*Efficiency- time *is money. Have your staff focus on their core business and have the corporate travel manager handle all the logistics for their travel including airfare, hotel cars and events TO MAXIMIZE EFFICIENCY AND KEEP YOUR STAFF FOCUSED ON YOUR CORE BUSINESS

*unforeseen circumstances* – the corporate travel manager handleS any cancellations, missed flights, canceled flights. Quick rebooking, and repositioning, and dealing with getting credits and reimbursement is extremely difficult and time-consuming. The corporate travel manager handles all of that SO YOU CAN CONTINUE ON SCHEDULE WITHOUT SPENDING HOURS REBOOKING AND GETTING CREDIT

Efficient and organized business travel management-help reduce travel expenses, streamline expense reports, optimize booking processes, and make managing the corporate travel experience way easier for all stakeholders involved.

Travel Support

Report on travel spend: In order to optimize their budgets, businesses need to know which departments are spending what on travel. Agencies can report on spend for all stakeholders by team, department, or project, and help you accurately track all your travel expenses.

Maintain compliance: Every company has some sort of rules that make up their travel policy. An agency can enforce these guidelines when booking.

Velnor Trips is a global leader in business travel management services. We drive savings, efficiency and safety to businesses and their travelers all around the world.

If you are looking for a tailored travel management solution, delivering customer service excellence, and a demonstrable return on investment, then you’ve come to the right place

Corporate travel policy compliance
Travel management reports
Meetings and event management
Travel program management
Dedicated travel counselor teams

By listening to your needs and focusing on your goals we can help your company design a global corporate travel service program that controls costs, improves traveler satisfaction and fits your corporate culture.

Our qualified business travel agents and cutting-edge technology deliver solutions that provide the best travel arrangements and travel policy adherence in the business. From CEO to support staff, our services can help make corporate travel a more efficient and enjoyable experience for everyone involved.

With so much involved in travel – from booking and expenses to meetings and strategy – you need the backing of a proven leader…
Velnor Trips, We’re your corporate travel partner to help you manage it all.

```html
<!DOCTYPE html>
<html lang="en">
<head>
<meta charset="utf-8">
<title>Velnor Trips – Travel Management Service</title>
<link href="https://fonts.googleapis.com/css2?family=Poppins:wght@400;500;600;700&family=Montserrat:wght@300;400&display=swap" rel="stylesheet">
<style>
:root{
  --navy:#0b1a3a;
  --ice:#d3effa;
  --ice-line:#bfe6f6;
  --white:#ffffff;
  --ink:#121826;
}
*{margin:0;padding:0;box-sizing:border-box}
html,body{width:869px;height:1200px;overflow:hidden;background:var(--white)}
body{font-family:'Poppins',sans-serif;color:var(--ink);position:relative}
.abs{position:absolute}

/* header */
.header-shapes{left:0;top:0}
.brand{left:0;width:540px;top:236px;text-align:center;color:var(--white)}
.brand-name{font-family:'Montserrat',sans-serif;font-weight:300;font-size:32px;letter-spacing:.12em}
.page-title{left:54px;top:344px;font-weight:700;font-size:22px;line-height:30px;color:var(--navy);letter-spacing:.01em}

/* section headings */
.section-head{display:flex;align-items:center;left:54px}
.section-head svg{display:block}
.section-head .label{position:absolute;left:56px;color:var(--white);font-weight:500;font-size:19px;line-height:20px}
.body-copy{font-size:11.7px;line-height:15.3px;color:var(--ink)}

/* why box */
.why-box{left:434px;top:408px;width:395px;height:465px;background:var(--navy)}
.why-title{left:460px;top:408px;width:345px;height:39px;font-weight:700;font-size:19px;color:var(--navy);text-align:center;line-height:39px}
.why-copy{left:471px;top:473px;width:326px;color:var(--white);font-size:11.8px;line-height:21.3px}

/* features */
.feature-bar{left:54px;top:1058px;width:775px;height:70px;background:var(--navy)}
.feature{background:var(--ice);border-radius:3px;top:1050px;height:60px;display:flex;align-items:center;padding-left:17px;font-weight:700;font-size:12px;line-height:14.5px;color:var(--navy)}
.feature-icon{width:32px;height:32px;border-radius:50%;background:var(--white);border:2px solid var(--ice-line);top:1063px;display:flex;align-items:center;justify-content:center}

/* footer */
.footer-item{font-size:12.4px;color:var(--navy);display:flex;align-items:center;gap:7px;line-height:15px}
.phone{left:30px;top:1160px;color:var(--white);font-weight:700;font-size:17.5px;display:flex;align-items:center;gap:9px}
</style>
</head>
<body>

<svg class="abs header-shapes" width="869" height="390" viewBox="0 0 869 390">
  <defs>
    <linearGradient id="travelerTone" x1="0" y1="0" x2="1" y2="1">
      <stop offset="0" stop-color="#dfe9f2"/>
      <stop offset=".5" stop-color="#5c7398"/>
      <stop offset="1" stop-color="#e8eef3"/>
    </linearGradient>
  </defs>
  <rect x="0" y="331" width="869" height="56" fill="var(--ice)"/>
  <polygon points="0,0 560,0 456,186 534,331 0,331" fill="var(--navy)"/>
  <polygon points="556,0 869,0 869,378 564,378 454,186" fill="var(--ice)"/>
  <polygon points="566,0 869,0 869,378 576,378 466,186" fill="url(#travelerTone)" role="img" aria-label="Photo of business travelers walking through an airport with rolling suitcases"/>
</svg>

<div class="abs brand">
  <div class="brand-name">VELNOR TRIPS</div>
</div>

<div class="abs page-title">TRAVEL MANAGEMENT SERVICE</div>

<div class="abs section-head" style="top:411px">
  <svg width="300" height="40" viewBox="0 0 300 40">
    <polygon points="30,3 268,3 284,37 30,37" fill="var(--navy)"/>
    <line x1="273" y1="3" x2="290" y2="37" stroke="var(--navy)" stroke-width="2"/>
    <circle cx="20" cy="20" r="19" fill="var(--white)" stroke="var(--navy)" stroke-width="2.5"/>
    <circle cx="20" cy="20" r="14" fill="var(--ice)"/>
    <path d="M12 24 q4 -3 8 0 h6 l4-3" fill="none" stroke="var(--navy)" stroke-width="1.4"/>
    <circle cx="21" cy="14" r="4" fill="none" stroke="var(--navy)" stroke-width="1.3"/>
  </svg>
  <span class="label">UNPARALLED SERVICE</span>
</div>
<p class="abs body-copy" style="left:57px;top:465px;width:356px">Velnor Trips is famous for our concierge style approach to travel. From detailed planning, to commercial or private air travel, transportation, including car rentals, chauffers, busses for larger groups, hotels, all styles of lodging accomodations, special event planning and more, Velnor Trips is like having your own personal or corporate travel butler.</p>

<div class="abs section-head" style="top:585px">
  <svg width="300" height="40" viewBox="0 0 300 40">
    <polygon points="30,3 236,3 252,37 30,37" fill="var(--navy)"/>
    <line x1="241" y1="3" x2="258" y2="37" stroke="var(--navy)" stroke-width="2"/>
    <circle cx="20" cy="20" r="19" fill="var(--white)" stroke="var(--navy)" stroke-width="2.5"/>
    <circle cx="20" cy="20" r="14" fill="var(--ice)"/>
    <circle cx="20" cy="20" r="8" fill="none" stroke="var(--navy)" stroke-width="1.4"/>
    <path d="M20 15 v5 l4 2" fill="none" stroke="var(--navy)" stroke-width="1.4"/>
  </svg>
  <span class="label">EFFICIENCY- TIME</span>
</div>
<p class="abs body-copy" style="left:54px;top:637px;width:356px">Time is your most valuable tool! Our goal at Velnor Trips is to have your employees’ complete focus be on your core business, while having us handle all the logistics for their travel. One of the most appreciated services we offer is the management of travel headaches. Unforeseen circumstances such as cancellations, missed flights, cancelled flights, last minute bookings or changed plans, can take hours to rectify. Velnor Trips handles all of these tedious repositionings expeditiously, saving your employees precious time. Give your company a competitive edge by having Velnor Trips handle your team’s travel arrangements.</p>

<div class="abs section-head" style="top:851px;left:52px">
  <svg width="300" height="48" viewBox="0 0 300 48">
    <polygon points="30,4 272,4 288,44 30,44" fill="var(--navy)"/>
    <line x1="277" y1="4" x2="294" y2="44" stroke="var(--navy)" stroke-width="2"/>
    <circle cx="22" cy="24" r="21" fill="var(--white)" stroke="var(--navy)" stroke-width="2.5"/>
    <circle cx="22" cy="24" r="15" fill="var(--ice)"/>
    <rect x="13" y="19" width="18" height="10" fill="none" stroke="var(--navy)" stroke-width="1.4"/>
    <line x1="11" y1="31" x2="33" y2="31" stroke="var(--navy)" stroke-width="1.4"/>
  </svg>
  <span class="label" style="left:58px">BUDGET AND TRAVEL<br>&nbsp;SPEND REPORTING</span>
</div>
<p class="abs body-copy" style="left:54px;top:914px;width:764px">Having a travel management service will ensure that your company enforces corporate compliance and maintains control over travel decisions. This ensures that your employees stick to your budget, which in turn will protect your bottom line. Travel expenses can be costly. Having a savvy and experienced corporate travel manager who can access deep discounts not available to the public will ensure your travel is booked across the board at the lowest prices expenses are kept under control. Travel reporting is critical to optimizing budgets, streamlining expense reports, and recognizing key trends. Velnor-Trips customizes travel spend reports, by team, project, department etc, so companies can accurately track travel expenses, and make critical decisions based on the spend.</p>

<div class="abs why-box"></div>
<svg class="abs" style="left:460px;top:408px" width="345" height="40" viewBox="0 0 345 40">
  <polygon points="0,0 345,0 325,39 22,39" fill="var(--ice)"/>
</svg>
<div class="abs why-title">WHY CHOOSE VELNOR TRIPS?</div>
<p class="abs why-copy">Velnor Trips is a global leader in business travel management services. We drive savings, efficiency, and unparaleled service to businesses and their travelers all around the world. If you are looking for a tailored travel managed solution focused on offering white glove service and fulfilling your individual preferences ,while delivering customer excellence, you’ve come to the right place.<br>At Velnor Trips, our mission is to have you focus on your day to day business while we handle all of the logistics and details for the most successful all encompassing travel experience. From emergency passport arrangements to last minute cancellations, re-bookings, and other intricate travel challenges, Velnor Trips is well versed in handling the routine array of travel services, as well as solving any travel related issue that might arise.</p>

<div class="abs feature-bar"></div>
<div class="abs feature" style="left:75px;width:120px">WHITE GLOVE<br>SERVICE</div>
<div class="abs feature" style="left:227px;width:133px">CORPORATE<br>TRAVEL POLICY<br>COMPLIANCE</div>
<div class="abs feature" style="left:387px;width:127px;padding-left:20px">STREAMLINED<br>EXPENSE<br>REPORTS</div>
<div class="abs feature" style="left:543px;width:127px;padding-left:16px">UNPARALLELED<br>SAVINGS</div>
<div class="abs feature" style="left:698px;width:127px;padding-left:17px">FULL SERVICE<br>TRAVEL<br>MANAGEMENT</div>

<div class="abs feature-icon" style="left:55px"><svg width="16" height="16" viewBox="0 0 16 16"><path d="M3 4 l3 9 h6 l1-6 -3 1 -1-5 -2 5 z" fill="var(--navy)"/></svg></div>
<div class="abs feature-icon" style="left:206px"><svg width="16" height="16" viewBox="0 0 16 16"><circle cx="8" cy="8" r="6" fill="none" stroke="var(--navy)" stroke-width="1.4"/><path d="M2 8 h12 M8 2 q-4 6 0 12 q4-6 0-12" fill="none" stroke="var(--navy)" stroke-width="1"/></svg></div>
<div class="abs feature-icon" style="left:373px"><svg width="18" height="16" viewBox="0 0 18 16"><circle cx="6" cy="9" r="4" fill="none" stroke="var(--navy)" stroke-width="2" stroke-dasharray="2 1.3"/><circle cx="13" cy="5" r="3" fill="none" stroke="var(--navy)" stroke-width="1.8" stroke-dasharray="1.6 1.1"/></svg></div>
<div class="abs feature-icon" style="left:521px"><svg width="16" height="16" viewBox="0 0 16 16"><path d="M2 2 h10 l2 2 v10 h-12 z" fill="var(--navy)"/><rect x="5" y="3" width="5" height="3" fill="var(--white)"/><rect x="4.5" y="9" width="7" height="4" fill="var(--white)"/></svg></div>
<div class="abs feature-icon" style="left:678px"><svg width="16" height="16" viewBox="0 0 16 16"><circle cx="10" cy="4" r="2.3" fill="var(--navy)"/><path d="M6 15 v-5 q0-3 4-3 q4 0 4 3 v5 z" fill="var(--navy)"/><rect x="1" y="9" width="6" height="1.6" fill="var(--navy)"/></svg></div>

<svg class="abs" style="left:0;top:1150px" width="869" height="50" viewBox="0 0 869 50">
  <rect x="220" y="5" width="649" height="40" fill="var(--ice)"/>
  <rect x="220" y="45" width="649" height="5" fill="var(--navy)"/>
  <polygon points="0,2 226,2 250,50 0,50" fill="var(--navy)"/>
  <line x1="232" y1="2" x2="256" y2="50" stroke="var(--navy)" stroke-width="2"/>
</svg>
<div class="abs phone">
  <svg width="16" height="16" viewBox="0 0 16 16"><path d="M4 2 l3 3 -2 2 q1 3 4 4 l2-2 3 3 -2 2 q-6 0 -10-10 z" fill="none" stroke="var(--white)" stroke-width="1.5"/></svg>
  212-555-0187
</div>
<div class="abs footer-item" style="left:273px;top:1159px">
  <svg width="15" height="13" viewBox="0 0 15 13"><rect x="1" y="2" width="13" height="10" fill="none" stroke="var(--navy)" stroke-width="1.4"/><path d="M1 2 l6.5 6 6.5-6" fill="none" stroke="var(--navy)" stroke-width="1.4"/></svg>
  info@velnor-trips.com
</div>
<div class="abs footer-item" style="left:436px;top:1159px">
  <svg width="13" height="16" viewBox="0 0 13 16"><path d="M6.5 15 q-5-6-5-9 a5 5 0 0 1 10 0 q0 3-5 9z" fill="none" stroke="var(--navy)" stroke-width="1.4"/><circle cx="6.5" cy="6" r="1.8" fill="var(--navy)"/></svg>
  <span>310 Ardent Avenue suite 1204<br>New York City, NY 10016</span>
</div>
<div class="abs footer-item" style="left:661px;top:1162px">
  <svg width="15" height="15" viewBox="0 0 15 15"><circle cx="7.5" cy="7.5" r="6" fill="none" stroke="var(--navy)" stroke-width="1.3"/><path d="M1.5 7.5 h12 M7.5 1.5 q-4 6 0 12 q4-6 0-12" fill="none" stroke="var(--navy)" stroke-width="1"/></svg>
  www.velnor-trips.com
</div>

</body>
</html>
```